GlassHaven Artbook for Okanagan Region, British Columbia

Creating an art book: GlassHaven, for the Okanagan Wine Region in British Columbia, Canada. Would like smart, modern, clean and linear...cool, sexy urban, not ugly boring suburban... I need a cover that appeals to the wino in all of us! Title: GlassHaven -Marla Dovicki
Updates
Thank you all kindly for your efforts. I have added some files so that you can get a sense of my aesthetic...it's never easy trying to figure it out, is it? I will hopefully have dimensions of book soon...cheers, Marla
would anyone please design a giant wine bottle with the wine label that looks like a label but says glasshaven...just curious to see if it works as a design or not...thank you.
Target Market(s)
Designing this wine art book of quotes to wineries in Okanagan BC. Buyer is wine lover and tourist ready to spend his vacation bucks on this wonderful book!
Look and feel

```html
<!DOCTYPE html>
<html lang="en">
<head>
<meta charset="utf-8">
<title>GlassHaven — Marla Dovicki</title>
<link href="https://fonts.googleapis.com/css2?family=Questrial&display=swap" rel="stylesheet">
<style>
  :root {
    --paper: #ffffff;
    --rose: #ff4a85;
    --band-raspberry: #ff2146;
    --band-red: #ff0d0d;
    --band-scarlet: #ff0505;
    --band-deep: #cc0000;
    --glass-area: rgba(255, 255, 255, 0.28);
    --type: "Questrial", "Century Gothic", sans-serif;
  }
  html, body {
    margin: 0;
    padding: 0;
    overflow: hidden;
    background: var(--paper);
  }
  .cover {
    display: block;
    width: 1200px;
    height: 1136px;
  }
  .cover-title,
  .cover-author {
    font-family: var(--type);
  }
  .title-upper { fill: var(--rose); }
  .title-lower { fill: var(--paper); }
  .cover-author { fill: var(--paper); }
</style>
</head>
<body>
<svg class="cover" viewBox="0 0 1200 1136" width="1200" height="1136" xmlns="http://www.w3.org/2000/svg">
  <g class="colour-bands">
    <rect class="band band-paper" x="0" y="0" width="1200" height="430" fill="var(--paper)"/>
    <rect class="band band-rose" x="0" y="430" width="1200" height="53" fill="var(--rose)"/>
    <rect class="band band-raspberry" x="0" y="483" width="1200" height="89" fill="var(--band-raspberry)"/>
    <rect class="band band-red" x="0" y="572" width="1200" height="141" fill="var(--band-red)"/>
    <rect class="band band-scarlet" x="0" y="713" width="1200" height="177" fill="var(--band-scarlet)"/>
    <rect class="band band-deep" x="0" y="890" width="1200" height="246" fill="var(--band-deep)"/>
  </g>

  <rect class="glass-illustration" role="img" aria-label="White wine glass silhouette holding wine, rising from the bottom edge"
        x="77" y="430" width="383" height="706" rx="40" fill="var(--glass-area)"/>

  <g class="cover-title">
    <text class="title-upper" x="96" y="430" font-size="250">Glass</text>
    <text class="title-lower" x="501" y="630" font-size="219">Haven</text>
  </g>

  <text class="cover-author" x="1146" y="1058" font-size="40" text-anchor="end">Marla Dovicki</text>
</svg>
</body>
</html>
```